PSD Website Design

I am looking to have a custom website designed. I would like a PSD made of the design I came up with. Once I get the design I will slice the PSD and create a wordpress template from it.

See attachment for basic layout of the graphic. The image labeled Player page is the basic page I will need for the website. I also need a home page with an image slider on it and thumbnails of recent, state video uploads.

A textured background is ok.

Looking for a quick turnaround.

Text at top of page is a menu that is needed. Open to seeing the menu as a navigational bar or/and with different font types.

No preference on page background color or font colors. I welcome creativity.

```html
<!DOCTYPE html>
<html lang="en">
<head>
<meta charset="utf-8">
<title>Summit Prospect Scouting – Player Profile</title>
<link href="https://fonts.googleapis.com/css2?family=Oswald:wght@400;500&family=Open+Sans:wght@400;600&family=Ubuntu:wght@400&display=swap" rel="stylesheet">
<style>
:root{
  --orange:#e8740e;
  --red:#c8262a;
  --page:#dedfe3;
  --panel:#ffffff;
  --ink:#333333;
  --muted:#888888;
  --link:#2a6fb5;
  --blue:#5bc6ea;
  --dark:#282828;
  --footer:#3b3b3b;
  --footer-deep:#1f1f1f;
  --field:#9c9c9c;
}
*{margin:0;padding:0;box-sizing:border-box}
html,body{width:843px;height:1200px;overflow:hidden}
body{position:relative;font-family:"Open Sans",sans-serif;color:var(--ink);
  background:var(--page) repeating-linear-gradient(45deg,rgba(255,255,255,.25) 0 1px,transparent 1px 3px);}
.heading{font-family:"Oswald",sans-serif;font-weight:500;color:var(--orange);text-transform:uppercase;letter-spacing:-.2px}

/* header */
.site-header{position:absolute;left:0;top:0;width:843px;height:68px;background:#fff;border-bottom:4px solid var(--orange)}
.brand{position:absolute;left:80px;top:14px;display:flex;align-items:center;gap:6px;font-family:"Oswald",sans-serif;font-weight:500;font-size:23px;color:#1e1e1e;letter-spacing:.5px}
.brand-mark{width:12px;height:12px;background:var(--orange)}
.brand-sub{position:absolute;left:98px;top:44px;font-size:7.5px;letter-spacing:2px;font-weight:600;color:#1e1e1e}
.main-nav{position:absolute;left:319px;top:30px;display:flex;gap:22px;font-family:"Ubuntu",sans-serif;font-size:14px;color:#777}
.main-nav .active{color:var(--orange);position:relative}
.main-nav .active::after{content:"";position:absolute;left:50%;top:29px;margin-left:-6px;border:6px solid transparent;border-bottom-color:var(--orange)}
.search{position:absolute;left:653px;top:28px;width:102px;height:21px;border:1px solid #bbb;border-radius:3px;background:#eee;font-size:9px;font-style:italic;color:#999;padding:4px 7px}
.search-btn{position:absolute;right:0;top:0;width:22px;height:19px;background:#ccc;border-left:1px solid #aaa}

/* panel */
.content{position:absolute;left:74px;top:78px;width:686px;height:912px;background:var(--panel)}
.player-photo{position:absolute;left:84px;top:100px;width:180px;height:220px;background:#fff;padding:7px;box-shadow:1px 2px 5px rgba(0,0,0,.35);transform:rotate(-1deg)}
.player-photo div{width:100%;height:100%;background:linear-gradient(160deg,#d7e6b3,#bcd48c)}
.player-info{position:absolute;left:278px;top:100px;width:152px;font-size:8.5px;line-height:14.5px}
.player-info h1{font-family:"Open Sans",sans-serif;font-weight:600;font-size:18px;color:#222;line-height:24px}
.player-info .pos{color:var(--link);font-size:9.5px;font-weight:600;margin-bottom:2px}
.player-info p{border-bottom:1px solid #eee}
.class-of{position:absolute;left:275px;top:284px;font-size:9.5px;font-weight:600;color:#6b8f1c}

/* game film */
.film-rule{position:absolute;left:457px;top:108px;width:292px;height:3px;background:#555}
.film-label{position:absolute;left:533px;top:92px;width:132px;height:34px;background:var(--red);border-radius:0 0 6px 6px;text-align:center;line-height:34px;font-family:"Oswald",sans-serif;font-size:17px;color:#fff}

.thumb{position:absolute;width:93px;font-size:6px;line-height:8px;color:var(--muted)}
.thumb .img{height:52px;position:relative;margin-bottom:4px}
.thumb .img span{position:absolute;right:1px;bottom:1px;background:#000;color:#fff;font-size:5px;padding:0 2px}
.thumb b{display:block;color:var(--link);font-weight:400;font-size:6.5px;line-height:8px;margin-bottom:2px;height:16px;overflow:hidden}
.g1{background:linear-gradient(160deg,#5d7a3f,#8a8f6a)}
.g2{background:linear-gradient(160deg,#4e6b36,#a09a82)}
.g3{background:linear-gradient(160deg,#6f7f80,#3e5a33)}
.g4{background:linear-gradient(160deg,#2a8fd6,#c73a2a)}
.g5{background:linear-gradient(160deg,#a88c70,#c93a2a)}
.g6{background:linear-gradient(160deg,#3a9ad8,#d83b2a)}
.g7{background:linear-gradient(160deg,#d8d8c8,#c43a2a)}
.channel{position:absolute;font-size:6px;color:var(--muted)}
.channel strong{font-size:8px;color:#222;font-weight:600;margin-right:3px}
.channel i{display:inline-block;width:9px;height:9px;border-radius:50%;background:#222;vertical-align:-1px;margin-right:4px}

/* highlights */
.section-rule{position:absolute;height:2px;background:linear-gradient(90deg,var(--orange),rgba(232,116,14,.1))}
.section-title{position:absolute;font-size:17px;background:#fff;padding:0 5px}
.video{position:absolute;left:87px;top:405px;width:382px;height:235px;background:linear-gradient(180deg,#dfe3e6,#9b3a48 70%,#2a2a2a);box-shadow:0 6px 10px rgba(0,0,0,.25)}
.video-bar{position:absolute;left:0;bottom:0;width:100%;height:15px;background:#1b1b1b;color:#bbb;font-size:6px;padding:4px 60px}
.video-bar::before{content:"";position:absolute;left:12px;top:4px;border-left:7px solid #ddd;border-top:4px solid transparent;border-bottom:4px solid transparent}
.ad{position:absolute;left:535px;top:405px;width:211px;height:211px;background:#c4c4c4;color:#fff;font-family:"Oswald",sans-serif;font-size:20px;display:flex;align-items:center;justify-content:center}

/* tabs */
.tab{position:absolute;top:690px;height:30px;width:115px;background:#eee;border:1px solid #ddd;border-bottom:none;font-family:"Oswald",sans-serif;font-size:15px;color:var(--orange);text-align:center;padding-top:4px;white-space:nowrap}
.tab.active{background:#fff;border:2px solid #e5e5e5;border-bottom:none;top:691px;height:28px}
.tab-box{position:absolute;left:87px;top:718px;width:389px;height:239px;border:2px solid #e5e5e5;background:#fff}
.subscribe{position:absolute;left:435px;top:836px;background:var(--red);color:#fff;font-size:5.5px;padding:1px 4px;border-radius:2px}

/* viral */
.viral{position:absolute;left:501px;top:723px;width:249px;height:234px;background:var(--dark);border-radius:3px}
.event{position:absolute;left:513px;top:760px;width:224px;height:73px;background:#fff;border-radius:2px;font-size:10px;line-height:15px;padding:7px 6px;color:#222}
.event-tag{position:absolute;left:513px;top:741px;background:#fff;font-family:"Oswald",sans-serif;font-size:17px;color:#111;padding:0 5px;height:22px;line-height:22px}
.connect{position:absolute;left:487px;top:845px;width:250px;height:28px;background:var(--blue);color:#fff;font-family:"Oswald",sans-serif;font-size:16px;padding:2px 29px}
.connect-fold{position:absolute;left:487px;top:873px;border-top:12px solid #2b8db3;border-left:14px solid transparent}
.social{position:absolute;top:891px;width:45px;height:44px;border-radius:6px;background:linear-gradient(#fafafa,#d6d6d6);border-bottom:3px solid var(--blue);font-size:8px;font-weight:600;color:#555;display:flex;align-items:center;justify-content:center}

/* footer */
.site-footer{position:absolute;left:0;top:990px;width:843px;height:182px;background:var(--footer);border-top:4px solid #555}
.footer-col{position:absolute;color:#eee}
.footer-col h2{font-family:"Oswald",sans-serif;font-weight:500;color:var(--orange);font-size:17px;padding-bottom:7px;margin-bottom:9px}
.quick h2{border-bottom:1px solid #555;width:140px;padding-left:20px;margin-left:-20px}
.quick li{list-style:none;font-size:12.5px;line-height:21.5px}
.contact-line{position:relative;font-size:12.5px;line-height:16px;padding-left:20px;margin-bottom:12px}
.contact-line svg{position:absolute;left:0;top:2px}
.field{position:absolute;background:var(--field);border:1px solid #bbb;color:#eee;font-size:11.5px;font-style:italic;padding:1px 6px}
.send{position:absolute;left:691px;top:1135px;width:58px;height:21px;background:var(--orange);color:#fff;font-size:12px;text-align:center;line-height:21px}
.copyright{position:absolute;left:0;top:1172px;width:843px;height:28px;background:var(--footer-deep);color:#ddd;font-size:11.5px;padding:6px 82px}
</style>
</head>
<body>

<header class="site-header">
  <div class="brand"><span class="brand-mark"></span>SUMMIT</div>
  <div class="brand-sub">PROSPECT SCOUTING</div>
  <nav class="main-nav"><span>Home</span><span>About us</span><span>State</span><span class="active">Position</span><span>Join</span></nav>
  <div class="search">search here...<span class="search-btn"></span></div>
</header>

<main class="content"></main>

<div class="player-photo"><div role="img" aria-label="Portrait photo of the player in a yellow sleeveless shirt"></div></div>
<section class="player-info">
  <h1>Marcus Delaney</h1>
  <div class="pos">Wide Receiver</div>
  <p>Miami, FL (Bayview Central)</p>
  <p>Ht: 6-1.5 &nbsp;|&nbsp; Wt: 197</p>
  <p>40 Time: 4.45</p>
  <p>Bench: 22 Reps</p>
  <p>Vertical: 36</p>
  <p style="border:none">5-10-5 Shuttle: 4.42</p>
</section>
<div class="class-of">CLASS OF 2015</div>

<div class="film-rule"></div>
<div class="film-label">GAME FILM</div>

<div class="thumb" style="left:460px;top:150px"><div class="img g1" role="img" aria-label="Video thumbnail"><span>9:56</span></div><b>Spring Camp Drills and Route Work</b>by fieldreel 10,820,629 views<br>3 years ago</div>
<div class="thumb" style="left:558px;top:150px"><div class="img g2" role="img" aria-label="Video thumbnail"><span>7:54</span></div><b>Combine Day Recap</b>by coachcam22 10,358 views<br>3 years ago</div>
<div class="thumb" style="left:656px;top:150px"><div class="img g3" role="img" aria-label="Video thumbnail"><span>6:23</span></div><b>Senior Season Game Film Top Plays</b>by sidelinepro 32,118 views<br>4 years ago</div>
<div class="channel" style="left:460px;top:258px"><i></i><strong>gridironreel</strong>Popular channel on the site - we think you'll like it</div>
<div class="thumb" style="left:460px;top:273px"><div class="img g4" role="img" aria-label="Video thumbnail"><span>23:45</span></div><b>Camp Drill Series Footwork Ladder</b>by gridironreel 17,498,131 views<br>1 year ago</div>
<div class="thumb" style="left:558px;top:273px"><div class="img g5" role="img" aria-label="Video thumbnail"><span>4:47</span></div><b>Catch Drills at Practice</b>by gridironreel 4,842,690 views<br>2 years ago</div>
<div class="thumb" style="left:656px;top:273px"><div class="img g6" role="img" aria-label="Video thumbnail"><span>13:33</span></div><b>Route Tree Breakdown Session</b>by gridironreel 10,769,905 views<br>2 years ago</div>

<div class="section-rule" style="left:86px;top:381px;width:390px"></div>
<div class="heading section-title" style="left:106px;top:369px">HIGHLIGHTS</div>
<div class="video" role="img" aria-label="Highlight video of a team huddle at an indoor training facility"><div class="video-bar">0:12 / 7:50</div></div>
<div class="ad">ADVERTISEMENT SPOT</div>

<div class="tab active" style="left:87px">RECENT RECRUITS</div>
<div class="tab" style="left:210px">FLORIDA</div>
<div class="tab" style="left:334px">MOST VIEWED</div>
<div class="tab-box"></div>

<div class="thumb" style="left:95px;top:732px"><div class="img g1" role="img" aria-label="Video thumbnail"><span>9:56</span></div><b>Spring Camp Drills and Route Work</b>by fieldreel 10,820,629 views<br>3 years ago</div>
<div class="thumb" style="left:190px;top:732px"><div class="img g2" role="img" aria-label="Video thumbnail"><span>7:54</span></div><b>Combine Day Recap</b>by coachcam22 10,358 views<br>3 years ago</div>
<div class="thumb" style="left:285px;top:732px"><div class="img g3" role="img" aria-label="Video thumbnail"><span>6:23</span></div><b>Senior Season Game Film Top Plays</b>by sidelinepro 32,118 views<br>4 years ago</div>
<div class="thumb" style="left:380px;top:732px"><div class="img g1" role="img" aria-label="Video thumbnail"><span>6:30</span></div><b>Seven on Seven Highlights</b>by fieldreel 11,410 views<br>2 years ago</div>
<div class="channel" style="left:95px;top:837px"><i></i><strong>gridironreel</strong>Popular channel on the site - we think you'll like it</div>
<div class="subscribe">Subscribe</div>
<div class="thumb" style="left:95px;top:853px"><div class="img g4" role="img" aria-label="Video thumbnail"><span>23:45</span></div><b>Camp Drill Series Footwork Ladder</b>by gridironreel 17,498,131 views<br>1 year ago</div>
<div class="thumb" style="left:190px;top:853px"><div class="img g5" role="img" aria-label="Video thumbnail"><span>4:47</span></div><b>Catch Drills at Practice</b>by gridironreel 4,842,690 views<br>2 years ago</div>
<div class="thumb" style="left:285px;top:853px"><div class="img g6" role="img" aria-label="Video thumbnail"><span>13:33</span></div><b>Route Tree Breakdown Session</b>by gridironreel 10,769,905 views<br>2 years ago</div>
<div class="thumb" style="left:380px;top:853px"><div class="img g7" role="img" aria-label="Video thumbnail"><span>13:17</span></div><b>Fall Camp Scrimmage Reel</b>by gridironreel 9,619,796 views<br>1 year ago</div>

<div class="section-rule" style="left:497px;top:704px;width:263px"></div>
<div class="heading section-title" style="left:510px;top:692px">TAKE IT VIRAL</div>
<div class="viral"></div>
<div class="event">Lorem ipsum dolor sit amet,consectetuer adipiscing elit, sed diam nonummy nibh euismod tincidunt ut laoreet dolore magna aliquam erat volutpat.</div>
<div class="event-tag">NEXT EVENT</div>
<div class="connect">CONNECT WITH SUMMIT</div>
<div class="connect-fold"></div>
<div class="social" style="left:515px">Post</div>
<div class="social" style="left:573px">Chat</div>
<div class="social" style="left:632px">Watch</div>
<div class="social" style="left:690px">Photos</div>

<footer class="site-footer"></footer>
<div class="footer-col quick" style="left:100px;top:1009px">
  <h2>QUICK LINKS</h2>
  <ul><li>About us</li><li>Position</li><li>State</li><li>Join</li></ul>
</div>
<div class="footer-col" style="left:274px;top:1009px">
  <h2 style="margin-left:15px">CONTACT US</h2>
  <div class="contact-line"><svg width="11" height="13" viewBox="0 0 11 13"><path d="M5.5 0a5 5 0 0 0-5 5c0 4 5 8 5 8s5-4 5-8a5 5 0 0 0-5-5z" fill="#999"/><circle cx="5.5" cy="5" r="2" fill="#3b3b3b"/></svg>Address: 234 Street Name,<br>City, State 12345</div>
  <div class="contact-line"><svg width="12" height="12" viewBox="0 0 12 12"><path d="M2 0l3 3-1.5 1.5a8 8 0 0 0 4 4L9 7l3 3-2 2C5 12 0 7 0 2z" fill="#999"/></svg>1234-5677-8901</div>
  <div class="contact-line"><svg width="13" height="10" viewBox="0 0 13 10"><rect x=".5" y=".5" width="12" height="9" fill="none" stroke="#999"/><path d="M.5 .5l6 5 6-5" fill="none" stroke="#999"/></svg>contact@email.com</div>
</div>
<div class="footer-col" style="left:537px;top:1009px"><h2>GET IN TOUCH</h2></div>
<div class="field" style="left:539px;top:1044px;width:92px;height:21px">Name</div>
<div class="field" style="left:644px;top:1044px;width:107px;height:21px">Email</div>
<div class="field" style="left:539px;top:1072px;width:211px;height:57px;padding-top:5px">Your Message...</div>
<div class="send">Send</div>
<div class="copyright">© 2014 Summit Prospect Scouting, All Rights Reserved</div>

</body>
</html>
```